Dynamic Business Card for Sports Supplements Company

Hi! I'm looking for an awesome business card to match my existing sports supplement company. I have uploaded my current company logo and screenshot of the front page of my website.

I would like to have something dynamic and interesting and utilize the colors in the website - the reds and purples

The business card should be double sided and focus on a unique eye-catching design on the back and include all the relevant company info.

Most importantly, it should say somewhere: "Sign up on our website for a coupon code."

Target Market(s)

Mostly for women gym goers but it shouldn't be too feminine. It should be in keeping with the website design. It should flow and clearly be connected to it

Industry/Entity Type

Business

Contact Information for Business Card

Lorraine K. Vestal
CEO
LVestal@Quorvanexco.com
www.quorvanexco.com
555.417.3820
P.O. Box 47315
Alder Falls, Oregon 00000

Sign up on our website for a coupon code

Font styles to use
Serif
Sans Serif
Other font styles liked:
• Novecento font family and "Quorvanex" is in AR Destine font

Requirements
Must have
• One side should be a bold Quorvanex logo design. Even just the symbol itself may be o.k. (see attached file)

```html
<!DOCTYPE html>
<html lang="en">
<head>
<meta charset="utf-8">
<title>Quorvanex Business Card</title>
<link rel="stylesheet" href="https://fonts.googleapis.com/css2?family=Arimo:wght@400;700&display=swap">
<style>
  :root {
    --stage: #e9e7e4;
    --card: #161616;
    --card-edge: #222222;
    --red: #d8232a;
    --white: #f4f4f4;
    --grey: #a9a9a9;
    --divider: #4a4a4a;
  }
  * { box-sizing: border-box; margin: 0; padding: 0; }
  html, body { width: 1200px; height: 864px; overflow: hidden; }
  body {
    background: var(--stage);
    font-family: "Arimo", Arial, sans-serif;
    position: relative;
  }
  .card {
    position: absolute;
    width: 600px;
    height: 343px;
    background: var(--card);
    border: 1px solid var(--card-edge);
    box-shadow: 0 10px 28px rgba(0,0,0,0.25);
  }
  .card--back { left: 90px; top: 80px; }
  .card--front { left: 510px; top: 441px; }

  .brand-name {
    font-weight: 700;
    letter-spacing: 1px;
    display: inline-flex;
    align-items: center;
    gap: 12px;
    white-space: nowrap;
  }
  .brand-mark {
    display: inline-block;
    background: var(--red);
  }

  /* Back */
  .back-brand {
    position: absolute;
    left: 50%; top: 130px;
    transform: translateX(-50%);
  }
  .back-brand .brand-name { font-size: 44px; color: var(--grey); }
  .back-brand .brand-mark { width: 22px; height: 22px; }
  .coupon-note {
    margin-top: 24px;
    font-size: 13px;
    color: var(--grey);
    letter-spacing: 0.2px;
    text-align: center;
  }

  /* Front */
  .front-brand {
    position: absolute;
    left: 30px; top: 0; bottom: 0;
    width: 260px;
    display: flex;
    align-items: center;
    justify-content: center;
  }
  .front-brand .brand-name { font-size: 30px; color: var(--white); gap: 9px; }
  .front-brand .brand-mark { width: 15px; height: 15px; }
  .divider {
    position: absolute;
    left: 304px; top: 70px;
    width: 1px; height: 205px;
    background: var(--divider);
  }
  .contact {
    position: absolute;
    left: 330px; top: 78px;
    color: var(--white);
  }
  .contact-name { color: var(--red); font-size: 19px; letter-spacing: 0.4px; }
  .contact-title { font-size: 13px; margin-top: 3px; }
  .contact-address { font-size: 13px; line-height: 17px; margin-top: 14px; }
  .contact-list { list-style: none; margin-top: 10px; font-size: 13px; }
  .contact-list li {
    display: flex; align-items: center; gap: 8px;
    height: 21px;
    white-space: nowrap;
  }
  .contact-list svg { width: 12px; height: 12px; flex: none; }
</style>
</head>
<body>

<section class="card card--back" aria-label="Card back">
  <div class="back-brand">
    <div class="brand-name"><span class="brand-mark"></span>QUORVANEX</div>
    <p class="coupon-note">Sign up on our website for a coupon code</p>
  </div>
</section>

<section class="card card--front" aria-label="Card front">
  <div class="front-brand">
    <div class="brand-name"><span class="brand-mark"></span>QUORVANEX</div>
  </div>
  <div class="divider"></div>
  <div class="contact">
    <p class="contact-name">Lorraine K. Vestal</p>
    <p class="contact-title">CEO</p>
    <p class="contact-address">P.O. Box 47315<br>Alder Falls, Oregon 00000</p>
    <ul class="contact-list">
      <li>
        <svg viewBox="0 0 12 12" aria-hidden="true"><path fill="#d8232a" d="M2.5 1h2l1 2.5-1.3 1a6.5 6.5 0 0 0 3.3 3.3l1-1.3 2.5 1v2a1 1 0 0 1-1 1A9.5 9.5 0 0 1 1.5 2a1 1 0 0 1 1-1z"/></svg>
        555.417.3820
      </li>
      <li>
        <svg viewBox="0 0 12 12" aria-hidden="true"><rect x="0.5" y="2" width="11" height="8" rx="1" fill="#d8232a"/><path d="M1 2.8 6 6.5 11 2.8" fill="none" stroke="#161616" stroke-width="1"/></svg>
        LVestal@Quorvanexco.com
      </li>
      <li>
        <svg viewBox="0 0 12 12" aria-hidden="true"><circle cx="6" cy="6" r="5.5" fill="#d8232a"/><path d="M0.5 6h11M6 0.5c-2.5 3-2.5 8 0 11M6 0.5c2.5 3 2.5 8 0 11" fill="none" stroke="#161616" stroke-width="0.8"/></svg>
        www.quorvanexco.com
      </li>
    </ul>
  </div>
</section>

</body>
</html>
```